Beautify our counselling web application

I have a web application in development and at the moment it is very plain.
It has being developed with laravel and vue. I need a simple design for the user interface to make it look more sleek and professional. I will need someone who is able to code the design as part of the service. The app is very low-cost for voluntary and social enterprise services and we don't have a lot of money so I need someone who is just starting out or someone with a big heart.
I have uploaded current pages to show the contents.
I will tip for good work.

Target Market(s)

Counsellors and psychotherapists

Industry/Entity Type

SaaS

Font styles to use
Serif
Sans Serif

Colors
0054AA
0677BA
7BADD7
CADEEF
E8F1F8

Requirements
Must have
• Ability to code the design into the current site
Nice to have
• elegant, modern. cool, profession. nice examples include merovaultix.com quillbanter.com fenrodu.com
Should not have
• corny literal 90s icons, icons with more than one colour using primary colours

```html
<!DOCTYPE html>
<html lang="en">
<head>
<meta charset="utf-8">
<title>Counselling App – Screens</title>
<link href="https://fonts.googleapis.com/css2?family=Roboto:wght@400;500;700&display=swap" rel="stylesheet">
<style>
:root{
  --primary:#0054AA;
  --primary-2:#0677BA;
  --sky:#7BADD7;
  --pale:#CADEEF;
  --mist:#E8F1F8;
  --side-top:#0a80d6;
  --side-bottom:#0054AA;
  --ink:#2b2b2b;
  --line:#e3e3e3;
  --stage:#e4e4e4;
  --chip:#f5f5f5;
}
*{box-sizing:border-box;margin:0;padding:0}
html,body{width:705px;height:1200px;overflow:hidden;background:var(--stage);font-family:'Roboto',sans-serif;color:var(--ink)}
.screen{position:absolute;left:30px;width:645px;height:358px;background:#fff;overflow:hidden}
.sidebar{position:absolute;left:0;top:0;width:95px;height:100%;background:linear-gradient(180deg,var(--side-top),var(--side-bottom))}
.brand{position:absolute;left:10px;top:9px;color:#fff;font-weight:500;font-size:9px;line-height:10px}
.menu{list-style:none}
.menu li{position:absolute;left:0;width:95px;height:12px;display:flex;align-items:center;color:#fff;font-size:5.2px;font-weight:500}
.menu li svg{position:absolute;left:10px;width:6px;height:6px;fill:#fff}
.menu li span{position:absolute;left:22px}
.menu li .caret{position:absolute;left:77px;width:0;height:0;border-left:2.2px solid transparent;border-right:2.2px solid transparent;border-top:2.4px solid #fff}
.menu li.active::before{content:"";position:absolute;left:0;top:0;width:2px;height:12px;background:#fff;border-radius:0 2px 2px 0}
.toggle{position:absolute;left:88px;top:9px;width:13px;height:13px;background:#fff;border-radius:3px;box-shadow:0 1px 3px rgba(0,0,0,.15);display:flex;align-items:center;justify-content:center}
.topbar{position:absolute;left:95px;top:0;right:0;height:30px;background:#fff;box-shadow:0 2px 6px rgba(0,0,0,.05)}
.top-search{position:absolute;left:18px;top:8px;width:109px;height:15px;background:#f5f6f8;border-radius:3px;font-size:5.5px;color:#555;padding-left:7px;display:flex;align-items:center}
.top-search svg{position:absolute;right:7px;top:4px}
.icon-btn{position:absolute;top:8px;width:15px;height:15px;border-radius:50%;background:#f3f4f6;display:flex;align-items:center;justify-content:center}
.avatar{position:absolute;left:461px;top:6px;width:18px;height:18px;border-radius:50%;background:linear-gradient(135deg,#c9b39c,#6d8aa6);border:1.5px solid var(--primary)}
.user{position:absolute;left:483px;top:8px;font-size:6px;font-weight:500;line-height:7px}
.user small{display:block;color:var(--primary);font-size:4.5px;font-weight:400}
.chev{position:absolute;left:526px;top:13px}
.content{position:absolute;left:0;top:0;width:100%;height:100%}
.page-title{position:absolute;font-size:8px;font-weight:500;color:#222}
.filterbox{position:absolute;left:146px;top:60px;width:135px;height:18px;background:#fff;border-radius:3px;box-shadow:0 1px 4px rgba(0,0,0,.1);font-size:5.3px}
.filterbox .btn{position:absolute;left:1px;top:1.5px;width:35px;height:15px;background:#eef0f2;border-radius:2px;display:flex;align-items:center;justify-content:center;font-weight:500;gap:1.5px}
.filterbox .ph{position:absolute;left:45px;top:6px;color:#888}
.grid{position:absolute;left:105px;top:88px;width:523px}
.row{display:grid;grid-template-columns:21.3px 35px 77.5px 40.5px 64px 44px 50px 64px 67px auto;padding-left:5.7px;height:20.5px;align-items:center;font-size:5.3px;color:#333;border-left:1px solid var(--line);border-right:1px solid var(--line);border-bottom:1px solid var(--line)}
.row.head{height:18.5px;background:var(--primary);color:#fff;font-weight:500;border:none;border-radius:3px 3px 0 0}
.row.head .risk{font-size:6px}
.check{width:4.5px;height:4.5px;border:.6px solid #444;border-radius:.8px}
.banner{position:absolute;left:115px;top:82px;width:470px;height:32px;background:var(--primary);color:#fff;font-weight:700;font-size:15px;display:flex;align-items:center;justify-content:center}
.sub{position:absolute;left:115px;font-size:8px;font-weight:500;color:#222}
.link{position:absolute;left:115px;font-size:5.5px;color:var(--primary)}
.btn-primary{position:absolute;background:var(--primary);color:#fff;font-weight:500;font-size:6px;display:flex;align-items:center;justify-content:center;border-radius:3px}
.crumb{position:absolute;left:115px;top:64px;font-size:8.5px;font-weight:500}
.crumb a{color:var(--primary);text-decoration:none}
.crumb .sep{margin:0 6px;color:#333}
.tab{position:absolute;top:87px;width:77px;height:21.5px;background:var(--chip);border:1px solid #e2e2e2;font-size:6.2px;font-weight:500;display:flex;align-items:center;justify-content:center}
.panel{position:absolute;left:116px;top:118px;width:510px;height:100px;background:#fff;box-shadow:0 1px 6px rgba(0,0,0,.08)}
.episode{position:absolute;left:132px;top:129px;font-size:8px;font-weight:500;color:var(--primary)}
.started{position:absolute;left:189.5px;top:129px;font-size:8px;color:#555}
.started b{color:var(--primary);font-weight:500}
.tile{position:absolute;width:77px;height:21.5px;background:var(--mist);color:var(--primary);font-size:6.2px;font-weight:500;display:flex;align-items:center;justify-content:center}
</style>
</head>
<body>

<!-- Screen 1: Caseload -->
<section class="screen" style="top:31px">
  <aside class="sidebar">
    <div class="brand">Counselling<br>App</div>
    <ul class="menu">
      <li style="top:43px"><svg viewBox="0 0 10 10"><circle cx="5" cy="5" r="3.5"/><circle cx="5" cy="5" r="1.3" fill="#0a80d6"/></svg><span>Dashboard</span></li>
      <li class="active" style="top:61px"><svg viewBox="0 0 10 10"><rect x="1" y="3" width="8" height="6" rx="1"/><rect x="3.5" y="1.5" width="3" height="2" fill="none" stroke="#fff"/></svg><span>Caseload</span></li>
      <li style="top:80px"><svg viewBox="0 0 10 10"><circle cx="5" cy="5" r="4"/></svg><span>Calendar</span></li>
      <li style="top:100px"><svg viewBox="0 0 10 10"><circle cx="3" cy="3" r="1.6"/><circle cx="7" cy="3" r="1.6"/><rect x="1" y="5.5" width="8" height="3.5" rx="1.5"/></svg><span>Address Book</span></li>
      <li style="top:120px"><svg viewBox="0 0 10 10"><text x="2" y="9" font-size="10" font-weight="700" fill="#fff">$</text></svg><span>Users</span><i class="caret"></i></li>
      <li style="top:140px"><svg viewBox="0 0 10 10"><rect x="2" y="4.5" width="6" height="5" rx="1"/><path d="M3.5 4.5V3a1.5 1.5 0 013 0v1.5" fill="none" stroke="#fff"/></svg><span>Services</span></li>
      <li style="top:160px"><svg viewBox="0 0 10 10"><circle cx="5" cy="3" r="2"/><rect x="2" y="5.5" width="6" height="4" rx="1.5"/></svg><span>Clients</span><i class="caret"></i></li>
      <li style="top:180px"><svg viewBox="0 0 10 10"><ellipse cx="5" cy="4.5" rx="4" ry="3"/><path d="M2 7l-1 2 3-1z"/></svg><span>Audit</span></li>
      <li style="top:199px"><svg viewBox="0 0 10 10"><path d="M2 1l2 0 1 2.5-1.3 1a5 5 0 002 2l1-1.3 2.5 1v2a1 1 0 01-1 1A8 8 0 011 2a1 1 0 011-1z"/></svg><span>Monitoring</span><i class="caret"></i></li>
    </ul>
  </aside>
  <div class="toggle"><svg width="7" height="6" viewBox="0 0 7 6" stroke="#0677BA" stroke-width=".7"><path d="M0 .5h7M0 2.3h5M0 4h7M0 5.6h4"/></svg></div>
  <header class="topbar">
    <div class="top-search">Search<svg width="6" height="6" viewBox="0 0 10 10" fill="none" stroke="#222" stroke-width="1.6"><circle cx="4.2" cy="4.2" r="3"/><path d="M6.5 6.5L9 9"/></svg></div>
    <div class="icon-btn" style="left:385px"><svg width="7" height="7" viewBox="0 0 10 10" fill="none" stroke="#444" stroke-width=".9"><path d="M8.5 4A3.6 3.6 0 002 3M1.5 6a3.6 3.6 0 006.5 1M2 1v2h2M8 9V7H6"/></svg></div>
    <div class="icon-btn" style="left:406px"><svg width="7" height="7" viewBox="0 0 10 10" fill="none" stroke="#444" stroke-width=".9"><path d="M2.5 7.5V4.5a2.5 2.5 0 015 0v3l1 1h-7zM4 9.3h2"/></svg></div>
    <div class="icon-btn" style="left:427px"><svg width="7" height="7" viewBox="0 0 10 10" fill="none" stroke="#444" stroke-width=".9"><rect x="1" y="1.5" width="8" height="6" rx="1.5"/><path d="M3 7.5v2l2-2"/><circle cx="3.3" cy="4.5" r=".3"/><circle cx="5" cy="4.5" r=".3"/><circle cx="6.7" cy="4.5" r=".3"/></svg></div>
    <div class="icon-btn" style="left:448px"><svg width="7" height="7" viewBox="0 0 10 10" fill="none" stroke="#444" stroke-width=".9"><path d="M1 3.5V1h2.5M6.5 1H9v2.5M9 6.5V9H6.5M3.5 9H1V6.5"/></svg></div>
    <div class="avatar" role="img" aria-label="User profile photo"></div>
    <div class="user">John Doe<small>Admin</small></div>
    <svg class="chev" width="7" height="4" viewBox="0 0 7 4" fill="none" stroke="#0054AA" stroke-width=".9"><path d="M.5.5l3 3 3-3"/></svg>
  </header>
  <main class="content">
    <h1 class="page-title" style="left:105px;top:64px">Caseload</h1>
    <div class="filterbox"><div class="btn">Filter <svg width="3" height="2" viewBox="0 0 3 2"><path d="M0 0h3L1.5 2z"/></svg></div><span class="ph">Search...</span></div>
    <div class="grid">
      <div class="row head"><span class="risk">Risk</span><span>Alerts</span><span>Client</span><span>ID</span><span>Services</span><span>Therapist</span><span>Date of referral</span><span>First Contact</span><span>Previous Episode</span><span>Cntacts</span></div>
      <div class="row"><i class="check"></i><span></span><span>Lorem ipsum sit amet</span><span>002</span><span>Demo Services 1</span><span>Paul</span><span>05/07/2022</span><span>20/09/2022</span><span>-</span><span>Total : 03</span></div>
      <div class="row"><i class="check"></i><span></span><span>Lorem ipsum sit amet</span><span>003</span><span>Demo Services 1</span><span>Paul</span><span>13/07/2022</span><span>20/09/2022</span><span>-</span><span>Total : 02</span></div>
      <div class="row"><i class="check"></i><span></span><span>Lorem ipsum sit amet</span><span>004</span><span>Demo Services 1</span><span>Paul</span><span>19/08/2022</span><span>20/09/2022</span><span>-</span><span>Total : 03</span></div>
      <div class="row"><i class="check"></i><span></span><span>Lorem ipsum sit amet</span><span>005</span><span>Demo Services 1</span><span>Paul</span><span>17/07/2022</span><span>20/09/2022</span><span>-</span><span>Total : 03</span></div>
      <div class="row"><span></span><span></span><span>Lorem ipsum sit amet</span><span>006</span><span>Demo Services 1</span><span>Paul</span><span>23/08/2022</span><span>20/09/2022</span><span>29/11/2022</span><span>Total : 0</span></div>
      <div class="row"><i class="check"></i><span></span><span>Lorem ipsum sit amet</span><span>007</span><span>Demo Services 1</span><span>Mike</span><span>06/07/2022</span><span>20/09/2022</span><span>-</span><span>Total : 02</span></div>
    </div>
  </main>
</section>

<!-- Screen 2: Dashboard -->
<section class="screen" style="top:421px">
  <aside class="sidebar">
    <div class="brand">Counselling<br>App</div>
    <ul class="menu">
      <li class="active" style="top:43px"><svg viewBox="0 0 10 10"><circle cx="5" cy="5" r="3.5"/><circle cx="5" cy="5" r="1.3" fill="#0a80d6"/></svg><span>Dashboard</span></li>
      <li style="top:61px"><svg viewBox="0 0 10 10"><rect x="1" y="3" width="8" height="6" rx="1"/><rect x="3.5" y="1.5" width="3" height="2" fill="none" stroke="#fff"/></svg><span>Caseload</span></li>
      <li style="top:80px"><svg viewBox="0 0 10 10"><circle cx="5" cy="5" r="4"/></svg><span>Calendar</span></li>
      <li style="top:100px"><svg viewBox="0 0 10 10"><circle cx="3" cy="3" r="1.6"/><circle cx="7" cy="3" r="1.6"/><rect x="1" y="5.5" width="8" height="3.5" rx="1.5"/></svg><span>Address Book</span></li>
      <li style="top:120px"><svg viewBox="0 0 10 10"><text x="2" y="9" font-size="10" font-weight="700" fill="#fff">$</text></svg><span>Users</span><i class="caret"></i></li>
      <li style="top:140px"><svg viewBox="0 0 10 10"><rect x="2" y="4.5" width="6" height="5" rx="1"/><path d="M3.5 4.5V3a1.5 1.5 0 013 0v1.5" fill="none" stroke="#fff"/></svg><span>Services</span></li>
      <li style="top:160px"><svg viewBox="0 0 10 10"><circle cx="5" cy="3" r="2"/><rect x="2" y="5.5" width="6" height="4" rx="1.5"/></svg><span>Clients</span><i class="caret"></i></li>
      <li style="top:180px"><svg viewBox="0 0 10 10"><ellipse cx="5" cy="4.5" rx="4" ry="3"/><path d="M2 7l-1 2 3-1z"/></svg><span>Audit</span></li>
      <li style="top:199px"><svg viewBox="0 0 10 10"><path d="M2 1l2 0 1 2.5-1.3 1a5 5 0 002 2l1-1.3 2.5 1v2a1 1 0 01-1 1A8 8 0 011 2a1 1 0 011-1z"/></svg><span>Monitoring</span><i class="caret"></i></li>
    </ul>
  </aside>
  <div class="toggle"><svg width="7" height="6" viewBox="0 0 7 6" stroke="#0677BA" stroke-width=".7"><path d="M0 .5h7M0 2.3h5M0 4h7M0 5.6h4"/></svg></div>
  <header class="topbar">
    <div class="top-search">Search<svg width="6" height="6" viewBox="0 0 10 10" fill="none" stroke="#222" stroke-width="1.6"><circle cx="4.2" cy="4.2" r="3"/><path d="M6.5 6.5L9 9"/></svg></div>
    <div class="icon-btn" style="left:385px"><svg width="7" height="7" viewBox="0 0 10 10" fill="none" stroke="#444" stroke-width=".9"><path d="M8.5 4A3.6 3.6 0 002 3M1.5 6a3.6 3.6 0 006.5 1M2 1v2h2M8 9V7H6"/></svg></div>
    <div class="icon-btn" style="left:406px"><svg width="7" height="7" viewBox="0 0 10 10" fill="none" stroke="#444" stroke-width=".9"><path d="M2.5 7.5V4.5a2.5 2.5 0 015 0v3l1 1h-7zM4 9.3h2"/></svg></div>
    <div class="icon-btn" style="left:427px"><svg width="7" height="7" viewBox="0 0 10 10" fill="none" stroke="#444" stroke-width=".9"><rect x="1" y="1.5" width="8" height="6" rx="1.5"/><path d="M3 7.5v2l2-2"/><circle cx="3.3" cy="4.5" r=".3"/><circle cx="5" cy="4.5" r=".3"/><circle cx="6.7" cy="4.5" r=".3"/></svg></div>
    <div class="icon-btn" style="left:448px"><svg width="7" height="7" viewBox="0 0 10 10" fill="none" stroke="#444" stroke-width=".9"><path d="M1 3.5V1h2.5M6.5 1H9v2.5M9 6.5V9H6.5M3.5 9H1V6.5"/></svg></div>
    <div class="avatar" role="img" aria-label="User profile photo"></div>
    <div class="user">John Doe<small>Admin</small></div>
    <svg class="chev" width="7" height="4" viewBox="0 0 7 4" fill="none" stroke="#0054AA" stroke-width=".9"><path d="M.5.5l3 3 3-3"/></svg>
  </header>
  <main class="content">
    <h1 class="page-title" style="left:115px;top:64px">Dashboard</h1>
    <div class="banner">Welcome to Demo</div>
    <h2 class="sub" style="top:131px">Notifications</h2>
    <div class="btn-primary" style="left:115px;top:144px;width:75px;height:17px">Create Notification</div>
    <h2 class="sub" style="top:174px">No Notifications</h2>
    <h2 class="sub" style="top:198px">Today</h2>
    <p class="link" style="top:212px">No Appointments!</p>
    <h2 class="sub" style="top:235px">Reviews</h2>
    <p class="link" style="top:248px">No Reviews!</p>
  </main>
</section>

<!-- Screen 3: Client workspace -->
<section class="screen" style="top:810px">
  <aside class="sidebar">
    <div class="brand">Counselling<br>App</div>
    <ul class="menu">
      <li style="top:43px"><svg viewBox="0 0 10 10"><circle cx="5" cy="5" r="3.5"/><circle cx="5" cy="5" r="1.3" fill="#0a80d6"/></svg><span>Dashboard</span></li>
      <li class="active" style="top:61px"><svg viewBox="0 0 10 10"><rect x="1" y="3" width="8" height="6" rx="1"/><rect x="3.5" y="1.5" width="3" height="2" fill="none" stroke="#fff"/></svg><span>Caseload</span></li>
      <li style="top:80px"><svg viewBox="0 0 10 10"><circle cx="5" cy="5" r="4"/></svg><span>Calendar</span></li>
      <li style="top:100px"><svg viewBox="0 0 10 10"><circle cx="3" cy="3" r="1.6"/><circle cx="7" cy="3" r="1.6"/><rect x="1" y="5.5" width="8" height="3.5" rx="1.5"/></svg><span>Address Book</span></li>
      <li style="top:120px"><svg viewBox="0 0 10 10"><text x="2" y="9" font-size="10" font-weight="700" fill="#fff">$</text></svg><span>Users</span><i class="caret"></i></li>
      <li style="top:140px"><svg viewBox="0 0 10 10"><rect x="2" y="4.5" width="6" height="5" rx="1"/><path d="M3.5 4.5V3a1.5 1.5 0 013 0v1.5" fill="none" stroke="#fff"/></svg><span>Services</span></li>
      <li style="top:160px"><svg viewBox="0 0 10 10"><circle cx="5" cy="3" r="2"/><rect x="2" y="5.5" width="6" height="4" rx="1.5"/></svg><span>Clients</span><i class="caret"></i></li>
      <li style="top:180px"><svg viewBox="0 0 10 10"><ellipse cx="5" cy="4.5" rx="4" ry="3"/><path d="M2 7l-1 2 3-1z"/></svg><span>Audit</span></li>
      <li style="top:199px"><svg viewBox="0 0 10 10"><path d="M2 1l2 0 1 2.5-1.3 1a5 5 0 002 2l1-1.3 2.5 1v2a1 1 0 01-1 1A8 8 0 011 2a1 1 0 011-1z"/></svg><span>Monitoring</span><i class="caret"></i></li>
    </ul>
  </aside>
  <div class="toggle"><svg width="7" height="6" viewBox="0 0 7 6" stroke="#0677BA" stroke-width=".7"><path d="M0 .5h7M0 2.3h5M0 4h7M0 5.6h4"/></svg></div>
  <header class="topbar">
    <div class="top-search">Search<svg width="6" height="6" viewBox="0 0 10 10" fill="none" stroke="#222" stroke-width="1.6"><circle cx="4.2" cy="4.2" r="3"/><path d="M6.5 6.5L9 9"/></svg></div>
    <div class="icon-btn" style="left:385px"><svg width="7" height="7" viewBox="0 0 10 10" fill="none" stroke="#444" stroke-width=".9"><path d="M8.5 4A3.6 3.6 0 002 3M1.5 6a3.6 3.6 0 006.5 1M2 1v2h2M8 9V7H6"/></svg></div>
    <div class="icon-btn" style="left:406px"><svg width="7" height="7" viewBox="0 0 10 10" fill="none" stroke="#444" stroke-width=".9"><path d="M2.5 7.5V4.5a2.5 2.5 0 015 0v3l1 1h-7zM4 9.3h2"/></svg></div>
    <div class="icon-btn" style="left:427px"><svg width="7" height="7" viewBox="0 0 10 10" fill="none" stroke="#444" stroke-width=".9"><rect x="1" y="1.5" width="8" height="6" rx="1.5"/><path d="M3 7.5v2l2-2"/><circle cx="3.3" cy="4.5" r=".3"/><circle cx="5" cy="4.5" r=".3"/><circle cx="6.7" cy="4.5" r=".3"/></svg></div>
    <div class="icon-btn" style="left:448px"><svg width="7" height="7" viewBox="0 0 10 10" fill="none" stroke="#444" stroke-width=".9"><path d="M1 3.5V1h2.5M6.5 1H9v2.5M9 6.5V9H6.5M3.5 9H1V6.5"/></svg></div>
    <div class="avatar" role="img" aria-label="User profile photo"></div>
    <div class="user">John Doe<small>Admin</small></div>
    <svg class="chev" width="7" height="4" viewBox="0 0 7 4" fill="none" stroke="#0054AA" stroke-width=".9"><path d="M.5.5l3 3 3-3"/></svg>
  </header>
  <main class="content">
    <nav class="crumb"><a href="#">CaseLoad</a><span class="sep">/</span>Daniel Morrow</nav>
    <div class="tab" style="left:116px">Workspace</div>
    <div class="tab" style="left:205px">Client information</div>
    <div class="tab" style="left:294px">Client Record</div>
    <div class="tab" style="left:383px">Client Progress</div>
    <div class="tab" style="left:472px">Payment</div>
    <div class="panel"></div>
    <div class="episode">Episode 01</div>
    <div class="started"><b>Started</b> : Wed Sep 14 2022</div>
    <div class="btn-primary" style="left:540px;top:124px;width:76px;height:20px;border-radius:0">End Episode</div>
    <div class="tile" style="left:132px;top:156px">Session Record</div>
    <div class="tile" style="left:213px;top:156px">Assessment</div>
    <div class="tile" style="left:295px;top:156px">Risk Mangement</div>
    <div class="tile" style="left:376px;top:156px">Treatment</div>
    <div class="tile" style="left:457.5px;top:156px">Safeguarding</div>
    <div class="tile" style="left:539px;top:156px">Consent</div>
    <div class="tile" style="left:132px;top:182px">Questionnaire</div>
    <div class="tile" style="left:213px;top:182px">Document</div>
    <div class="tile" style="left:295px;top:182px">Non-Clinical note</div>
    <div class="tile" style="left:376px;top:182px">Summary</div>
    <div class="tile" style="left:457.5px;top:182px">Timeline</div>
  </main>
</section>

</body>
</html>
```